Copper Field Agency Website - Wordpress Web UPDATED BRIEF

FINAL LOGO UPLOADED - please look to this as reference for how we would like the site to look and feel.

We are a digital marketing agency - looking to have a new website built. We are looking for a simple one page feel of site that will allow us to grow it later. (Feel free to take some liberties with that if your imagination veers off) Must be very, playful, bold, sleek and easily integrate video. Wordpress only.

Overview:

Copper Field is a creative constellation. We are built on what's great about the shared economy. With access to thousands of content creators, designers, technicians, writers, strategists and other creatives around the world, we are built differently than a traditional “brick and mortar” Marketing Agency. We provide the traditional services our clients have come to expect, without the “5X factor” of covering the overhead common in the old agency model. We believe even better work can be created in collaboration with our clients and by passing those savings back to them for their use. Our clients pay for our art, our work and our passion –not our furniture.

"Copper Field, Let's Build Together"

Target Market(s)

companies looking for creative agency help, video production, creative consulting and coaching

Industry/Entity Type

Digital Marketing

Coding

Coded - Design and coding required

Number of Pages Required

1 page

Font styles to use
Sans Serif

Colors
3277b5
33a6d7
ec1f27

Requirements
Must have
• Wordpress design is a must. Looking for a one sheet homepage - with sections that are all on the main front page. We will have videos to embed, and should be able to have client logos and easy access to show a variety of our creative work.
• Please look to the logo for how we would like the site to feel.
• Please think "icon process flow" instead of blocks of text (which we used to have). Use the text to explain what the process flow should represent - don't actually copy paste the text but show it visually in icons.
Nice to have
• innovation around how we show video content. solid colors complementary to our palette and aesthetic.
Should not have
• Standard HTML coding

```html
<!DOCTYPE html>
<html lang="en">
<head>
<meta charset="UTF-8">
<title>Copper Field Agency</title>
<link rel="stylesheet" href="https://fonts.googleapis.com/css2?family=Montserrat:wght@600;700;800&family=Open+Sans:wght@400;600;700&display=swap">
<style>
:root{
  --blue:#3277b5;
  --blue-dark:#1f5c9c;
  --sky:#33a6d7;
  --red:#ec1f27;
  --ink:#2b2b2b;
  --muted:#6d6d6d;
  --line:#e2e2e2;
  --white:#ffffff;
}
*{margin:0;padding:0;box-sizing:border-box}
html,body{width:1200px;height:4172px;overflow:hidden}
body{position:relative;background:var(--white);font-family:"Open Sans",Arial,sans-serif;color:var(--ink)}
.abs{position:absolute}
.heading{font-family:"Montserrat",Arial,sans-serif;font-weight:800;color:var(--blue);letter-spacing:.5px}
.section-title{text-align:center;font-size:40px;left:0;width:1200px}
.intro{left:190px;width:820px;text-align:center;font-size:13px;line-height:26px;color:var(--muted)}
.btn{display:inline-flex;align-items:center;gap:10px;background:var(--red);color:var(--white);font-family:"Montserrat",Arial,sans-serif;font-weight:700;font-size:13px;letter-spacing:.5px;height:46px;padding:0 26px;border-radius:23px;box-shadow:0 8px 18px rgba(236,31,39,.3)}
.btn svg{width:16px;height:16px}

/* hero */
.hero-bg{left:0;top:0}
.brand{left:120px;top:34px;display:flex;align-items:center;gap:10px;color:var(--white);font-family:"Montserrat",Arial,sans-serif;font-weight:700;font-size:18px}
.brand-dot{width:34px;height:34px;border-radius:50%;background:var(--white)}
.nav{left:388px;top:50px;display:flex;gap:31px;list-style:none}
.nav li{color:var(--white);font-size:15px;font-weight:600}
.mascot{left:92px;top:150px;width:400px;height:400px;border-radius:50%;border:14px solid var(--white);background:radial-gradient(circle at 50% 40%,#4fa0dc,#2a66a8 70%);box-shadow:0 16px 40px rgba(0,0,0,.25)}
.hero-copy{left:520px;top:188px;width:590px;text-align:right;color:var(--white)}
.hero-copy h1{font-family:"Montserrat",Arial,sans-serif;font-weight:700;font-size:34px;letter-spacing:.5px;white-space:nowrap}
.hero-copy p{font-size:13px;line-height:26px;margin:16px 0 22px 210px}
.dots{left:1030px;top:412px;display:flex;gap:8px}
.dots span{width:10px;height:10px;border-radius:50%;background:rgba(255,255,255,.55)}
.dots span:first-child{background:var(--white)}

/* clients */
.client-grid{left:104px;top:1058px;width:992px;display:grid;grid-template-columns:repeat(5,184px);gap:18px 18px}
.client{height:112px;border:1px solid var(--line);display:flex;align-items:center;justify-content:center;font-family:"Montserrat",Arial,sans-serif;font-weight:700;font-size:20px;color:#555;background:var(--white)}

/* about */
.about-art{left:80px;top:1460px;width:480px;height:300px;border-radius:12px;background:linear-gradient(135deg,#e9eef3,#c9d3dd)}
.about-copy{left:572px;top:1400px;width:540px}
.about-copy h2{font-size:40px;margin-bottom:22px}
.about-copy p{font-size:14px;line-height:30px;color:#444;margin-bottom:26px}

/* services */
.flow{left:0;top:2090px}
.service{width:200px;text-align:center}
.service .icon{width:124px;height:124px;margin:0 auto;border-radius:50%;background:var(--white);box-shadow:0 8px 24px rgba(0,0,0,.12);display:flex;align-items:center;justify-content:center}
.service .icon svg{width:54px;height:54px}
.service h3{font-family:"Montserrat",Arial,sans-serif;font-weight:600;font-size:18px;color:var(--blue);margin-top:18px;line-height:22px}
.badge{left:880px;top:2260px;width:200px;height:200px;border-radius:50%;background:var(--white);box-shadow:0 8px 24px rgba(0,0,0,.14);display:flex;align-items:center;justify-content:center}
.badge-inner{width:164px;height:164px;border-radius:50%;background:var(--blue);display:flex;align-items:center;justify-content:center;color:var(--white);font-family:"Montserrat",Arial,sans-serif;font-weight:800;font-size:20px;text-align:center;line-height:24px}

/* testimonials */
.quote-row{left:100px;top:2820px;width:1000px;display:flex;gap:20px}
.quote{flex:1;height:176px;background:var(--white);border-radius:8px;box-shadow:0 6px 20px rgba(0,0,0,.12);padding:20px 22px}
.quote-head{display:flex;gap:14px;align-items:center;margin-bottom:16px}
.avatar{width:50px;height:50px;border-radius:50%;background:#d3d8dd}
.quote-head b{display:block;font-size:14px}
.quote-head small{font-size:12px;color:var(--muted)}
.quote p{font-size:12px;line-height:20px;color:var(--muted)}
.arrow{top:2892px;width:28px;height:28px}

/* creative work */
.work-copy{left:88px;top:3228px;width:520px}
.work-copy h2{font-size:40px;margin-bottom:22px}
.work-copy p{font-size:14px;line-height:30px;color:#444;margin-bottom:30px}
.work-art{left:690px;top:3180px;width:460px;height:400px;border-radius:12px;background:linear-gradient(135deg,#eef2f6,#c7d2de)}

/* footer */
.foot-col h4{font-family:"Montserrat",Arial,sans-serif;font-weight:700;font-size:22px;margin-bottom:18px}
.foot-col p,.foot-col li{font-size:13px;line-height:22px;color:#444;list-style:none}
.foot-col .label{font-weight:600;color:var(--ink);margin-top:8px}
.newsletter{left:672px;top:3830px;width:460px;color:var(--white)}
.newsletter h4{font-family:"Montserrat",Arial,sans-serif;font-weight:700;font-size:30px;margin-bottom:16px}
.newsletter p{font-size:13px;line-height:22px;margin-bottom:26px}
.signup{display:flex;align-items:center;width:420px;height:52px;background:var(--white);border-radius:26px;padding:4px 4px 4px 24px}
.signup span{flex:1;font-size:13px;color:#888}
.signup b{background:var(--red);color:var(--white);height:44px;padding:0 34px;border-radius:22px;display:flex;align-items:center;font-size:14px}
.copyright{left:738px;top:4078px;color:var(--white);font-size:12px}
</style>
</head>
<body>

<!-- hero -->
<svg class="abs hero-bg" width="1200" height="800" viewBox="0 0 1200 800" aria-hidden="true">
  <defs>
    <linearGradient id="heroGrad" x1="0" y1="0" x2="1" y2="1">
      <stop offset="0" stop-color="#2d6db2"/>
      <stop offset="1" stop-color="#1b5aa0"/>
    </linearGradient>
  </defs>
  <path d="M0 0H1200V770C1080 770 980 660 860 600C700 520 520 440 300 380C170 345 70 350 0 372Z" fill="url(#heroGrad)"/>
  <path d="M1200 430C1090 420 1010 470 960 520C1030 560 1110 640 1200 690Z" fill="#33a6d7" opacity=".35"/>
  <path d="M0 0H520C380 90 200 140 0 150Z" fill="#33a6d7" opacity=".25"/>
</svg>
<div class="abs brand"><span class="brand-dot"></span>Copper Field</div>
<ul class="abs nav">
  <li>Home</li><li>Clients</li><li>About</li><li>Services</li><li>Testimonials</li><li>Creative Work</li><li>Contact</li>
</ul>
<div class="abs mascot" role="img" aria-label="Agency mascot illustration"></div>
<div class="abs hero-copy">
  <h1>WELCOME TO COPPER FIELD</h1>
  <p>Sed ut perspiciatis unde omnis iste natus error sit voluptatem accusantium doloremque laudantium</p>
  <span class="btn">READ MORE <svg viewBox="0 0 16 16"><circle cx="8" cy="8" r="7" fill="none" stroke="#fff" stroke-width="1.6"/><path d="M6.5 5l3 3-3 3" fill="none" stroke="#fff" stroke-width="1.6"/></svg></span>
</div>
<div class="abs dots"><span></span><span></span><span></span><span></span></div>

<!-- clients -->
<h2 class="abs heading section-title" style="top:904px">OUR CLIENTS</h2>
<p class="abs intro" style="top:962px">Sed ut perspiciatis unde omnis iste natus error sit voluptatem accusantium doloremque laudantium, totam rem aperiam, eaque ipsa quae ab illo inventore veritatis et quasi architecto beatae vitae dicta sunt explicabo.</p>
<div class="abs client-grid">
  <div class="client">Ashford County</div>
  <div class="client">The Workshop</div>
  <div class="client">Big Nimbus</div>
  <div class="client">Drift</div>
  <div class="client">Quintra</div>
  <div class="client">Firmline</div>
  <div class="client">Pretty Poise</div>
  <div class="client">Sprout Lab</div>
  <div class="client">Sunridge</div>
  <div class="client">Fernhouse</div>
</div>

<!-- about -->
<svg class="abs" style="left:0;top:1370px" width="700" height="520" viewBox="0 0 700 520" aria-hidden="true">
  <path d="M0 60C120 10 230 20 300 60C200 120 160 260 260 330C340 390 420 400 470 470C330 510 140 500 0 470Z" fill="#3277b5"/>
  <path d="M0 90C60 70 120 75 170 95C110 150 100 260 170 340C110 360 50 360 0 350Z" fill="#33a6d7" opacity=".5"/>
</svg>
<div class="abs about-art" role="img" aria-label="Laptop with a person presenting charts"></div>
<div class="abs about-copy">
  <h2 class="heading">ABOUT US</h2>
  <p>Copper Field is a creative constellation. We are built on what's great about the shared economy. With access to thousands of content creators, designers, technicians, writers, strategists and other creatives around the world, we are built differently than a traditional "brick and mortar" Marketing Agency.</p>
  <span class="btn">READ MORE <svg viewBox="0 0 16 16"><circle cx="8" cy="8" r="7" fill="none" stroke="#fff" stroke-width="1.6"/><path d="M6.5 5l3 3-3 3" fill="none" stroke="#fff" stroke-width="1.6"/></svg></span>
</div>

<!-- services -->
<h2 class="abs heading section-title" style="top:1958px">OUR SERVICES</h2>
<p class="abs intro" style="top:2018px">Sed ut perspiciatis unde omnis iste natus error sit voluptatem accusantium doloremque laudantium, totam rem aperiam, eaque ipsa quae ab illo inventore veritatis et quasi architecto beatae vitae dicta sunt explicabo.</p>
<svg class="abs flow" width="1200" height="600" viewBox="0 0 1200 600" aria-hidden="true">
  <path d="M208 110C180 250 200 300 208 390M460 110V390M708 110C740 250 730 300 708 390M208 110H708M208 390H708M708 260C800 260 860 268 880 270" fill="none" stroke="#d5dbe2" stroke-width="2" stroke-dasharray="6 6"/>
</svg>
<div class="abs service" style="left:108px;top:2138px"><div class="icon"><svg viewBox="0 0 48 48"><circle cx="20" cy="20" r="12" fill="none" stroke="#ec1f27" stroke-width="5"/><path d="M29 29l11 11" stroke="#ec1f27" stroke-width="6" stroke-linecap="round"/></svg></div><h3>Discovery</h3></div>
<div class="abs service" style="left:360px;top:2138px"><div class="icon"><svg viewBox="0 0 48 48"><path d="M24 6a13 13 0 0 0-8 23v5h16v-5A13 13 0 0 0 24 6z" fill="none" stroke="#ec1f27" stroke-width="4"/><rect x="17" y="37" width="14" height="4" fill="#ec1f27"/></svg></div><h3>Strategy</h3></div>
<div class="abs service" style="left:608px;top:2138px"><div class="icon"><svg viewBox="0 0 48 48"><path d="M28 4L12 27h11l-4 17 17-24H25z" fill="#ec1f27"/></svg></div><h3>Project<br>Management</h3></div>
<div class="abs service" style="left:108px;top:2418px"><div class="icon"><svg viewBox="0 0 48 48"><rect x="11" y="6" width="26" height="36" rx="3" fill="#ec1f27"/><path d="M17 16h14M17 23h14M17 30h9" stroke="#fff" stroke-width="3"/></svg></div><h3>Content</h3></div>
<div class="abs service" style="left:360px;top:2418px"><div class="icon"><svg viewBox="0 0 48 48"><path d="M6 42V20l10 7v-7l10 7v-7l10 7V8h6v34z" fill="#ec1f27"/></svg></div><h3>Production</h3></div>
<div class="abs service" style="left:608px;top:2418px"><div class="icon"><svg viewBox="0 0 48 48"><circle cx="24" cy="14" r="8" fill="#ec1f27"/><path d="M10 42c0-10 6-16 14-16s14 6 14 16z" fill="#ec1f27"/></svg></div><h3>Paid Media<br>and Coaching</h3></div>
<div class="abs badge"><div class="badge-inner">COPPER<br>FIELD</div></div>

<!-- testimonials -->
<svg class="abs" style="left:0;top:2680px" width="1200" height="380" viewBox="0 0 1200 380" aria-hidden="true">
  <path d="M0 200C300 120 800 100 1200 40V380H0Z" fill="#f3f5f7"/>
</svg>
<h2 class="abs heading section-title" style="top:2718px;font-weight:700;font-size:38px">What Our Clients Say's</h2>
<svg class="abs arrow" style="left:28px" viewBox="0 0 28 28" aria-hidden="true"><path d="M18 6l-8 8 8 8" fill="none" stroke="#3277b5" stroke-width="4"/></svg>
<svg class="abs arrow" style="left:1144px" viewBox="0 0 28 28" aria-hidden="true"><path d="M10 6l8 8-8 8" fill="none" stroke="#3277b5" stroke-width="4"/></svg>
<div class="abs quote-row">
  <div class="quote"><div class="quote-head"><span class="avatar"></span><div><b>Mara Holt</b><small>Lorem ipsum dolor sit</small></div></div><p>Lorem ipsum dolor sit amet consectetur adipiscing elit, sed do eiusmod tempor incididunt ut labore et dolore magna aliqua.</p></div>
  <div class="quote"><div class="quote-head"><span class="avatar"></span><div><b>Leon Pratt</b><small>Lorem ipsum dolor sit</small></div></div><p>Lorem ipsum dolor sit amet consectetur adipiscing elit, sed do eiusmod tempor incididunt ut labore et dolore magna aliqua.</p></div>
  <div class="quote"><div class="quote-head"><span class="avatar"></span><div><b>Iris Vane</b><small>Lorem ipsum dolor sit</small></div></div><p>Lorem ipsum dolor sit amet consectetur adipiscing elit, sed do eiusmod tempor incididunt ut labore et dolore magna aliqua.</p></div>
</div>

<!-- creative work -->
<svg class="abs" style="left:0;top:3380px" width="1200" height="420" viewBox="0 0 1200 420" aria-hidden="true">
  <path d="M1200 60C1080 120 960 200 700 250C900 250 1080 300 1200 360Z" fill="#3277b5"/>
  <path d="M1200 140C1120 180 1040 230 940 250C1040 260 1130 290 1200 320Z" fill="#33a6d7" opacity=".6"/>
</svg>
<div class="abs work-copy">
  <h2 class="heading">OUR CREATIVE WORK</h2>
  <p>Copper Field is a creative constellation. We are built on what's great about the shared economy. With access to thousands of content creators, designers, technicians, writers, strategists and other creatives around the world, we are built differently than a traditional "brick and mortar" Marketing Agency.</p>
  <span class="btn">VIEW MORE <svg viewBox="0 0 16 16"><circle cx="8" cy="8" r="7" fill="none" stroke="#fff" stroke-width="1.6"/><path d="M6.5 5l3 3-3 3" fill="none" stroke="#fff" stroke-width="1.6"/></svg></span>
</div>
<div class="abs work-art" role="img" aria-label="Screen showing portfolio pieces with a person pointing"></div>

<!-- footer -->
<svg class="abs" style="left:0;top:3700px" width="1200" height="472" viewBox="0 0 1200 472" aria-hidden="true">
  <path d="M520 472C470 320 530 130 730 60C880 10 1060 0 1200 20V472Z" fill="#1f5c9c"/>
  <path d="M1200 20C1100 10 980 30 900 80C1000 70 1110 90 1200 140Z" fill="#33a6d7" opacity=".4"/>
</svg>
<div class="abs foot-col" style="left:88px;top:3834px">
  <h4>Contact Us</h4>
  <p class="label">Email address</p>
  <p>hello@copperfield.example</p>
  <p class="label">Call us</p>
  <p>+1 555 014 2290</p>
</div>
<div class="abs foot-col" style="left:340px;top:3834px">
  <h4>Links</h4>
  <ul><li>Home</li><li>Clients</li><li>About</li><li>Services</li><li>Testimonials</li><li>Creative Work</li><li>Contact</li></ul>
</div>
<div class="abs newsletter">
  <h4>Newsletter</h4>
  <p>Lorem ipsum dolor sit amet, consectetur adipiscing elit, sed do eiusmod tempor incididunt ut</p>
  <div class="signup"><span>Enter Your Email Address</span><b>Sign Up</b></div>
</div>
<p class="abs copyright">© Copyright 2020. Copper Field Agency. All Rights Reserved</p>

</body>
</html>
```